Business Card for a mobile physiotherapy company

I need a layout for a business card for a mobile physiotherapy company.
Slogan is "Mobile Physiotherapy - Your Road To Recovery"
Phone number is 867-555-0142
Email VardenTherapy@postnest.ca (subject to change with website)
Website www.VardenTherapy.ca
My name and credentials: Luke Varden Luke Varden, BSc(kin), MPT, CAFCI, IMS
Information maybe included: Direct Billing, Services including Physiotherapy, IMS, acupuncture
Maybe include facebook and instagram logos
One side with the logo clean and sharp
Other side with details, try not to look too busy, keep everything concise

```html
<!DOCTYPE html>
<html lang="en">
<head>
<meta charset="utf-8">
<title>Varden Therapy – Business Card</title>
<link rel="stylesheet" href="https://fonts.googleapis.com/css2?family=Merriweather:wght@400;700&display=swap">
<style>
  :root {
    --backdrop: #3b3b3c;
    --card: #1d1d1f;
    --silver: #8d8f93;
    --brand-green: #2d7a58;
    --band-blue: #2e5d8f;
    --band-teal: #1d6a5c;
    --follow-blue: #2c5680;
    --ink-light: #f2f2f2;
    --ink-muted: #d6dbe2;
  }
  * { box-sizing: border-box; margin: 0; padding: 0; }
  html, body { width: 799px; height: 1200px; overflow: hidden; }
  body {
    background: var(--backdrop);
    font-family: "Merriweather", Georgia, serif;
    display: flex;
    flex-direction: column;
    align-items: center;
    justify-content: space-around;
    padding: 60px 0;
  }
  .card {
    position: relative;
    width: 600px;
    height: 345px;
    background: var(--card);
    border-radius: 22px;
    overflow: hidden;
    box-shadow: 0 14px 30px rgba(0,0,0,.45);
  }
  /* Front */
  .card-front { display: flex; align-items: center; justify-content: center; }
  .front-wordmark {
    color: var(--silver);
    font-weight: 700;
    font-size: 40px;
    letter-spacing: 6px;
    text-transform: uppercase;
  }
  /* Back */
  .band { position: absolute; left: 0; top: 0; width: 600px; height: 345px; }
  .back-wordmark {
    position: absolute; top: 38px; right: 40px;
    color: var(--brand-green);
    font-weight: 700; font-size: 26px; letter-spacing: 4px;
    text-transform: uppercase;
  }
  .identity { position: absolute; left: 34px; top: 100px; color: var(--ink-light); }
  .person-name { font-size: 24px; font-weight: 700; letter-spacing: 1px; text-transform: uppercase; }
  .credentials { font-size: 11px; color: var(--ink-muted); margin-top: 4px; }
  .contact-list { list-style: none; margin-top: 14px; }
  .contact-list li { display: flex; align-items: center; gap: 10px; font-size: 13px; line-height: 1.75; }
  .contact-list svg { width: 13px; height: 13px; fill: var(--ink-light); flex: none; }
  .slogan {
    position: absolute; left: 34px; bottom: 32px;
    color: var(--ink-light); font-size: 13px;
  }
  .social {
    position: absolute; right: 36px; bottom: 28px;
    display: flex; align-items: center; gap: 8px;
    color: var(--follow-blue); font-size: 12px;
  }
  .social-dot { width: 16px; height: 16px; border-radius: 50%; background: var(--band-blue); }
  .social-dot.alt { background: #b0407a; }
</style>
</head>
<body>
  <section class="card card-front" aria-label="Card front">
    <p class="front-wordmark">Varden Therapy</p>
  </section>

  <section class="card card-back" aria-label="Card back">
    <svg class="band" viewBox="0 0 600 345" aria-hidden="true">
      <defs>
        <linearGradient id="bandFill" x1="0" y1="0" x2="1" y2="1">
          <stop offset="0" stop-color="var(--band-blue)"/>
          <stop offset="1" stop-color="var(--band-teal)"/>
        </linearGradient>
      </defs>
      <polygon points="0,88 330,88 470,205 250,272 0,272" fill="url(#bandFill)"/>
    </svg>

    <p class="back-wordmark">Varden Therapy</p>

    <div class="identity">
      <h1 class="person-name">Luke Varden</h1>
      <p class="credentials">BSc(kin), MPT, CAFCI, IMS</p>
      <ul class="contact-list">
        <li><svg viewBox="0 0 24 24"><path d="M6.6 10.8a15 15 0 0 0 6.6 6.6l2.2-2.2a1 1 0 0 1 1-.25 11.4 11.4 0 0 0 3.6.57 1 1 0 0 1 1 1V20a1 1 0 0 1-1 1A17 17 0 0 1 3 4a1 1 0 0 1 1-1h3.5a1 1 0 0 1 1 1c0 1.25.2 2.45.57 3.57a1 1 0 0 1-.25 1z"/></svg>867-555-0142</li>
        <li><svg viewBox="0 0 24 24"><path d="M2 5h20v14H2z M3 6l9 7 9-7" fill="none" stroke="#f2f2f2" stroke-width="2"/></svg>VardenTherapy@postnest.ca</li>
        <li><svg viewBox="0 0 24 24"><circle cx="12" cy="12" r="9" fill="none" stroke="#f2f2f2" stroke-width="2"/><path d="M3 12h18M12 3c3 3 3 15 0 18M12 3c-3 3-3 15 0 18" fill="none" stroke="#f2f2f2" stroke-width="1.6"/></svg>www.VardenTherapy.ca</li>
      </ul>
    </div>

    <p class="slogan">Mobile Physiotherapy - Your Road To Recovery</p>

    <div class="social">
      <span>Follow us on</span>
      <span class="social-dot"></span>
      <span class="social-dot alt"></span>
    </div>
  </section>
</body>
</html>
```